Modern design company business card design

We are a design oriented construction firm. The owner is an architect and licensed General Contractor and accomplished furniture designer. We do new home construction and large scale remodeling and office design. We would like a design for our new business cards that is clean and modern, but relatable. We like the bright green color of our logo mixed with different shades of grey. We're also open to reinterpreting the logo.

Target Market(s)

Potential design clients,
Construction clients

Industry/Entity Type

Architecture

Contact Information for Business Card

Tall Maple Design | Build Inc. (optional with logo, Inc. optional)Jeffrey MorganOwner (optional)317.555.0148 cell317.431.8056 officejmorgan@greensquareinc.comwww.greensquareinc.com

Font styles to use
Sans Serif
Other font styles liked:
• Avenir

Requirements
Nice to have
• I like designs that have some continuity between the front and back, i.e. similar layouts or graphic elements that wrap around the card. I tend to prefer horizontal over vertical, but that's not a have to. I also tend to prefer white or recycled paper.

```html
<!DOCTYPE html>
<html lang="en">
<head>
<meta charset="utf-8">
<title>Tall Maple Design | Build — Business Card</title>
<link rel="stylesheet" href="https://fonts.googleapis.com/css2?family=Nunito+Sans:wght@400;600;700&display=swap">
<style>
  :root {
    --page: #ecebe8;
    --green: #3cb54a;
    --green-deep: #1f8f2e;
    --kraft: #bba68f;
    --grey: #8f9196;
    --white: #ffffff;
    --accent: #d7f08a;
  }
  * { box-sizing: border-box; margin: 0; padding: 0; }
  html, body {
    width: 1200px; height: 913px; overflow: hidden;
    background: var(--page);
    font-family: "Nunito Sans", "Avenir", sans-serif;
  }
  .sheet {
    position: relative; width: 1200px; height: 913px;
    display: flex; align-items: center; justify-content: center; gap: 40px;
  }
  .card {
    position: relative; width: 540px; height: 309px;
    border-radius: 22px; overflow: hidden;
    box-shadow: 0 6px 18px rgba(0,0,0,.18);
  }
  .card-art { position: absolute; inset: 0; }

  .brand {
    position: absolute; display: flex; align-items: center; gap: 8px;
    color: var(--white); font-weight: 600; font-size: 17px; white-space: nowrap;
  }
  .brand-dot {
    width: 12px; height: 12px; border-radius: 50%; background: var(--white); flex: none;
  }
  .front .brand { left: 34px; top: 142px; }
  .back .brand { right: 34px; top: 72px; }

  .identity { position: absolute; right: 30px; top: 34px; text-align: right; }
  .identity-name {
    color: var(--white); font-weight: 700; font-size: 19px; letter-spacing: .5px;
    text-transform: uppercase;
  }
  .identity-title { color: var(--accent); font-size: 13px; font-weight: 400; }

  .contacts {
    position: absolute; right: 30px; top: 120px;
    list-style: none; text-align: right;
    color: var(--white); font-size: 13.5px; line-height: 22px;
  }
  .contacts li { display: flex; justify-content: flex-end; align-items: center; gap: 8px; }
  .contact-icon {
    width: 15px; height: 15px; background: var(--white); border-radius: 2px;
    display: inline-flex; align-items: center; justify-content: center;
  }
  .contact-icon svg { width: 11px; height: 11px; }
</style>
</head>
<body>
<main class="sheet">

  <section class="card front" aria-label="Card front">
    <svg class="card-art" viewBox="0 0 540 309" preserveAspectRatio="none" aria-hidden="true">
      <defs>
        <linearGradient id="front-green" x1="0" y1="0" x2="0" y2="1">
          <stop offset="0" stop-color="#55c460"/>
          <stop offset="1" stop-color="#2fa83d"/>
        </linearGradient>
      </defs>
      <rect width="540" height="309" fill="url(#front-green)"/>
      <path d="M0,0 H270 A 430 430 0 0 1 196 309 H0 Z" fill="var(--grey)"/>
      <path d="M0,0 H254 A 430 430 0 0 1 180 309 H0 Z" fill="var(--kraft)"/>
    </svg>

    <p class="brand"><span class="brand-dot"></span>Tall Maple Design | Build</p>

    <header class="identity">
      <h1 class="identity-name">Dennis Holloway</h1>
      <p class="identity-title">Owner</p>
    </header>

    <ul class="contacts">
      <li>317.555.0172
        <span class="contact-icon"><svg viewBox="0 0 12 12"><rect x="2" y="1" width="8" height="10" rx="1" fill="none" stroke="var(--green-deep)" stroke-width="1.4"/></svg></span>
      </li>
      <li>317.555.0148
        <span class="contact-icon"><svg viewBox="0 0 12 12"><path d="M3 1 L5 3.5 L4 5 Q5.5 7.5 7 8 L8.5 7 L11 9 L9.5 11 Q3 10 1 2.5 Z" fill="var(--green-deep)"/></svg></span>
      </li>
      <li>www.tallmapleinc.example
        <span class="contact-icon"><svg viewBox="0 0 12 12"><circle cx="6" cy="6" r="4.5" fill="none" stroke="var(--green-deep)" stroke-width="1.2"/><path d="M1.5 6 H10.5 M6 1.5 Q3 6 6 10.5 M6 1.5 Q9 6 6 10.5" fill="none" stroke="var(--green-deep)" stroke-width="1"/></svg></span>
      </li>
      <li>officedholloway@tallmapleinc.example
        <span class="contact-icon"><svg viewBox="0 0 12 12"><rect x="1.5" y="3" width="9" height="6.5" fill="none" stroke="var(--green-deep)" stroke-width="1.2"/><path d="M1.5 3 L6 7 L10.5 3" fill="none" stroke="var(--green-deep)" stroke-width="1.2"/></svg></span>
      </li>
    </ul>
  </section>

  <section class="card back" aria-label="Card back">
    <svg class="card-art" viewBox="0 0 540 309" preserveAspectRatio="none" aria-hidden="true">
      <defs>
        <linearGradient id="back-green" x1="0" y1="0" x2="0" y2="1">
          <stop offset="0" stop-color="#4cc05a"/>
          <stop offset="1" stop-color="#15802a"/>
        </linearGradient>
      </defs>
      <rect width="540" height="309" fill="url(#back-green)"/>
      <path d="M120,0 A 400 400 0 0 0 540 238 V0 Z" fill="var(--grey)"/>
      <path d="M140,0 A 400 400 0 0 0 540 220 V0 Z" fill="var(--kraft)"/>
    </svg>

    <p class="brand"><span class="brand-dot"></span>Tall Maple Design | Build</p>
  </section>

</main>
</body>
</html>
```